BOLD PINE HEATING AND COOLING

Industry/Entity Type

Hvac

Requirements
Must have
• logo
My name: Gavin Pruszynski
Phone number 555-309-4461
Text:
Furnace and AC repairs
New furnace and AC installation
Ductwork
Gas lines
Water Tanks
Tankless water heaters
Nice to have
• Profesional modern look

```html
<!DOCTYPE html>
<html lang="en">
<head>
<meta charset="utf-8">
<title>Bold Pine Heating and Cooling – Business Cards</title>
<link href="https://fonts.googleapis.com/css2?family=Cinzel:wght@500&family=Montserrat:wght@400;500;600&display=swap" rel="stylesheet">
<style>
  :root{
    --bg:#d3d3ce;
    --card-light:#ffffff;
    --card-dark:#2f2f2f;
    --brand-blue:#1756a9;
    --brand-red:#d71f2b;
    --brand-green:#7cc243;
    --text-grey:#444444;
    --text-light:#ffffff;
  }
  *{box-sizing:border-box;margin:0;padding:0}
  html,body{width:1200px;height:1058px;overflow:hidden;background:var(--bg)}
  body{font-family:"Montserrat",sans-serif;position:relative}
  .card{position:absolute;left:250px;width:700px;height:400px;overflow:hidden;box-shadow:0 10px 24px rgba(0,0,0,.18)}
  .card--front{top:90px;background:var(--card-light)}
  .card--back{top:568px;background:var(--card-dark)}

  .front__band{position:absolute;left:0;top:0;width:700px;height:400px}
  .front__brand{position:absolute;left:48px;top:150px;width:260px;display:flex;align-items:center;gap:12px}
  .brand-dot{width:22px;height:22px;border-radius:50%;background:var(--brand-blue);flex:none}
  .brand-name{font-family:"Montserrat",sans-serif;font-weight:600;color:var(--brand-blue);font-size:21px;line-height:1.2;letter-spacing:.5px}
  .front__divider{position:absolute;left:355px;top:95px;width:2px;height:140px;background:var(--brand-green)}
  .front__contact{position:absolute;left:390px;top:80px}
  .person-name{font-family:"Cinzel",serif;font-weight:500;color:var(--brand-blue);font-size:24px;letter-spacing:1px}
  .person-role{font-size:15px;color:var(--text-grey);margin:4px 0 16px}
  .contact-line{display:flex;align-items:center;gap:10px;font-size:15px;color:var(--text-grey);margin-bottom:6px}
  .contact-line svg{width:13px;height:13px;flex:none}

  .back__brand{position:absolute;left:150px;top:110px;width:480px;display:flex;align-items:center;gap:18px}
  .back__brand .brand-dot{width:34px;height:34px}
  .back__brand .brand-name{font-size:34px}
  .back__services{position:absolute;left:60px;top:270px;color:var(--text-light);font-size:19px;line-height:1.6;font-weight:400}
  .sep{color:var(--brand-green);margin:0 6px}
</style>
</head>
<body>
  <section class="card card--front" aria-label="Business card front">
    <svg class="front__band" viewBox="0 0 700 400" aria-hidden="true">
      <path d="M0,380 L352,380" stroke="var(--brand-red)" stroke-width="5" fill="none"/>
      <path d="M0,389 L360,389 C395,389 402,330 445,330 L700,330 L700,400 L0,400 Z" fill="var(--brand-blue)"/>
    </svg>
    <div class="front__brand">
      <span class="brand-dot"></span>
      <span class="brand-name">BOLD PINE HEATING AND COOLING</span>
    </div>
    <div class="front__divider"></div>
    <div class="front__contact">
      <div class="person-name">GAVIN PRUSZYNSKI</div>
      <div class="person-role">Director</div>
      <div class="contact-line">
        <svg viewBox="0 0 24 24"><path fill="var(--brand-blue)" d="M6.6 10.8a15.1 15.1 0 006.6 6.6l2.2-2.2c.3-.3.7-.4 1-.2 1.1.4 2.3.6 3.6.6.6 0 1 .4 1 1V20c0 .6-.4 1-1 1C10.6 21 3 13.4 3 4c0-.6.4-1 1-1h3.5c.6 0 1 .4 1 1 0 1.3.2 2.5.6 3.6.1.3 0 .7-.2 1z"/></svg>
        <span>555-309-4461</span>
      </div>
      <div class="contact-line">
        <svg viewBox="0 0 24 24"><rect x="3" y="5" width="18" height="14" rx="1" fill="none" stroke="var(--brand-blue)" stroke-width="2"/><path d="M3 6l9 7 9-7" fill="none" stroke="var(--brand-blue)" stroke-width="2"/></svg>
        <span>info@boldpineheat.com</span>
      </div>
      <div class="contact-line">
        <svg viewBox="0 0 24 24"><circle cx="12" cy="12" r="9" fill="none" stroke="var(--brand-blue)" stroke-width="2"/><path d="M3 12h18M12 3c3 3 3 15 0 18M12 3c-3 3-3 15 0 18" fill="none" stroke="var(--brand-blue)" stroke-width="1.6"/></svg>
        <span>www.boldpineheat.com</span>
      </div>
    </div>
  </section>

  <section class="card card--back" aria-label="Business card back">
    <div class="back__brand">
      <span class="brand-dot"></span>
      <span class="brand-name">BOLD PINE HEATING AND COOLING</span>
    </div>
    <p class="back__services">
      Furnace and AC repairs<span class="sep">|</span>New furnace and AC installation<br>
      Ductwork<span class="sep">|</span>Gas lines<span class="sep">|</span>Water Tanks<span class="sep">|</span>Tankless water heaters
    </p>
  </section>
</body>
</html>
```